Duct Manufacturing Company new to the industry needs business card and stationary design

we are sheet metal duct manufacturers looking for a business card design to fit my new business logo.
nothing to crazy that will date, but want it to stand out from the crowed.
I'm sure you guys will work it out.

Contact Information for Business Card

Glen Marsh
Director

Address
17 Dorwell St
Tarrawong NSW 2631

0438 760 514

Sales@flowbend.com.au

Font styles to use
Other font styles liked:
• BankGothic md bt

Requirements
Nice to have
• Like the idea of corner rounded to match logo
• like to keep colours flowing
• font I like sharp square not rounded

```html
<!DOCTYPE html>
<html lang="en">
<head>
<meta charset="utf-8">
<title>Flowbend Industries – Business Card</title>
<link rel="stylesheet" href="https://fonts.googleapis.com/css2?family=Michroma&family=Exo+2:ital,wght@0,400;1,400;1,600;1,700&display=swap">
<style>
  :root {
    --page-bg: #e9e7e2;
    --brand-blue: #0b5fb8;
    --brand-blue-deep: #0a4c9c;
    --brand-blue-light: #1a86d6;
    --brand-green: #7cc242;
    --brand-green-dark: #4f9e1f;
    --paper: #ffffff;
    --card-w: 560px;
    --card-h: 320px;
    --radius: 18px;
  }
  * { box-sizing: border-box; margin: 0; padding: 0; }
  html, body { width: 1200px; height: 900px; overflow: hidden; }
  body {
    background: var(--page-bg);
    position: relative;
    font-family: "Exo 2", sans-serif;
  }
  .card {
    position: absolute;
    left: calc((1200px - var(--card-w)) / 2);
    width: var(--card-w);
    height: var(--card-h);
    border-radius: var(--radius);
    overflow: hidden;
    box-shadow: 0 10px 26px rgba(0,0,0,0.18);
  }

  /* Back of card */
  .card--back {
    top: 100px;
    background: radial-gradient(ellipse at 70% 60%, var(--brand-blue-light) 0%, var(--brand-blue) 55%, var(--brand-blue-deep) 100%);
    color: var(--paper);
  }
  .back__wordmark {
    position: absolute;
    left: 40px;
    top: 32px;
    font-family: "Michroma", sans-serif;
    font-size: 15px;
    line-height: 1.15;
    letter-spacing: 1px;
  }
  .back__url {
    position: absolute;
    left: 40px;
    top: 76px;
    font-size: 11px;
    letter-spacing: 3px;
  }
  .back__brand {
    position: absolute;
    left: 0; right: 0;
    top: 170px;
    display: flex;
    align-items: center;
    justify-content: center;
    gap: 16px;
    font-family: "Michroma", sans-serif;
    font-size: 34px;
    letter-spacing: 2px;
  }
  .back__dot {
    width: 22px; height: 22px;
    border-radius: 50%;
    background: var(--brand-green);
  }

  /* Front of card */
  .card--front {
    top: 480px;
    background: var(--paper);
  }
  .front__swoosh {
    position: absolute;
    inset: 0;
    width: 100%;
    height: 100%;
  }
  .front__wordmark {
    position: absolute;
    left: 48px;
    top: 52px;
    display: flex;
    align-items: center;
    gap: 10px;
    font-family: "Michroma", sans-serif;
    font-size: 17px;
    line-height: 1.2;
    color: var(--brand-blue);
    letter-spacing: 1px;
  }
  .front__dot {
    width: 14px; height: 14px;
    border-radius: 50%;
    background: var(--brand-green);
    flex: none;
  }
  .holder {
    position: absolute;
    right: 40px;
    top: 104px;
    text-align: right;
  }
  .holder__name {
    font-style: italic;
    font-weight: 700;
    font-size: 24px;
    color: var(--brand-blue);
    line-height: 1.1;
  }
  .holder__title {
    font-style: italic;
    font-size: 15px;
    color: var(--brand-green-dark);
  }
  .contact {
    position: absolute;
    right: 40px;
    top: 210px;
    list-style: none;
    text-align: right;
    color: var(--paper);
    font-style: italic;
    font-size: 13px;
    line-height: 18px;
  }
  .contact__line {
    display: flex;
    justify-content: flex-end;
    align-items: center;
    gap: 8px;
  }
  .contact__icon {
    width: 13px; height: 13px;
    flex: none;
  }
  .contact__spacer { width: 13px; flex: none; }
</style>
</head>
<body>

  <section class="card card--back" aria-label="Back of business card">
    <div class="back__wordmark">FLOWBEND<br>INDUSTRIES</div>
    <div class="back__url">www.flowbend.com</div>
    <div class="back__brand">
      <span class="back__dot"></span>
      <span>FLOWBEND</span>
    </div>
  </section>

  <section class="card card--front" aria-label="Front of business card">
    <svg class="front__swoosh" viewBox="0 0 560 320" preserveAspectRatio="none" aria-hidden="true">
      <path d="M0 140 C 140 175, 330 190, 560 190 L 560 320 L 0 320 Z" fill="var(--brand-green)"/>
      <path d="M0 152 C 140 188, 330 200, 560 198 L 560 320 L 0 320 Z" fill="var(--brand-blue)"/>
    </svg>

    <div class="front__wordmark">
      <span class="front__dot"></span>
      <span>FLOWBEND<br>INDUSTRIES</span>
    </div>

    <div class="holder">
      <p class="holder__name">Glen Marsh</p>
      <p class="holder__title">Director</p>
    </div>

    <ul class="contact">
      <li class="contact__line"><span>17 Dorwell St</span><span class="contact__spacer"></span></li>
      <li class="contact__line"><span>Tarrawong NSW 2631</span><span class="contact__spacer"></span></li>
      <li class="contact__line"><span>0438 760 514</span>
        <svg class="contact__icon" viewBox="0 0 16 16" aria-hidden="true"><path d="M4 1 L6.5 4.5 L5 6.5 C6 8.5 7.5 10 9.5 11 L11.5 9.5 L15 12 L13 15 C7 14.5 1.5 9 1 3 Z" fill="var(--brand-green)"/></svg>
      </li>
      <li class="contact__line"><span>Sales@flowbend.com.au</span>
        <svg class="contact__icon" viewBox="0 0 16 16" aria-hidden="true"><rect x="1" y="3.5" width="14" height="9" rx="1" fill="var(--brand-green)"/><path d="M1.5 4 L8 9 L14.5 4" fill="none" stroke="var(--brand-blue)" stroke-width="1.3"/></svg>
      </li>
      <li class="contact__line"><span>www.flowbend.com.au</span>
        <svg class="contact__icon" viewBox="0 0 16 16" aria-hidden="true"><circle cx="8" cy="8" r="7" fill="var(--brand-green)"/><path d="M1 8 H15 M8 1 C4.5 5 4.5 11 8 15 M8 1 C11.5 5 11.5 11 8 15" fill="none" stroke="var(--brand-blue)" stroke-width="1"/></svg>
      </li>
    </ul>
  </section>

</body>
</html>
```